Professional Services - letterhead / business cards

The company (velmora partners) will provide services to Investment Funds and large investors in Spain. I have recently chosen a logo that I am attaching.

I would like a simple stationary design that i could use as letter head, business cards and "with compliments" cards.

I am not quite sure which color I will mostly use for the logo, in the email signature I will probably lean towards the white background and grey letters. I am attaching my favourite options.

Target Market(s)

Large Multinationals, Investment funds and Law firms

Industry/Entity Type

Business

Requirements
Must have
• my details are:
Luis R. Abadal
Velmora Partners S.L.
Casa de Torrelumbre
Calle de Vientoalto 27
28014 Madrid
T: +34 (91) 387-2265
M: +34 (646) 819-054
e-mail: labadal@velmorapartners.com

```html
<!DOCTYPE html>
<html lang="en">
<head>
<meta charset="utf-8">
<title>Velmora Partners – Business Cards</title>
<link rel="stylesheet" href="https://fonts.googleapis.com/css2?family=Jost:ital,wght@0,400;1,300;1,400&display=swap">
<style>
  :root {
    --navy: #14197a;
    --navy-ink: #1a237e;
    --card-white: #ffffff;
    --text-grey: #7d7d82;
    --rule-grey: #cfcfd4;
    --stage: #e7e6e9;
  }
  * { margin: 0; padding: 0; box-sizing: border-box; }
  html, body { width: 1200px; height: 800px; overflow: hidden; }
  body {
    background: var(--stage);
    font-family: "Jost", "Century Gothic", sans-serif;
    position: relative;
  }
  .card {
    position: absolute;
    top: 250px;
    width: 520px;
    height: 300px;
    border-radius: 20px;
    box-shadow: 0 6px 18px rgba(0,0,0,0.18);
    overflow: hidden;
  }
  .card--front { left: 50px; background: var(--card-white); }
  .card--back { left: 630px; background: var(--navy); }

  .wordmark {
    position: absolute;
    left: 0; right: 0;
    text-align: center;
    font-weight: 400;
    font-style: normal;
    letter-spacing: 0.5px;
  }
  .card--front .wordmark { top: 44px; font-size: 34px; color: var(--navy-ink); }
  .card--back .wordmark { top: 100px; font-size: 40px; color: #ffffff; }

  .identity {
    position: absolute;
    top: 118px; left: 0; right: 0;
    text-align: center;
    font-style: italic;
  }
  .identity__name {
    font-size: 17px;
    font-weight: 400;
    color: var(--navy-ink);
    letter-spacing: 1px;
    text-transform: uppercase;
  }
  .identity__company, .identity__email {
    font-size: 11.5px;
    font-weight: 300;
    color: var(--text-grey);
    margin-top: 3px;
  }
  .identity__email strong { font-weight: 300; color: var(--navy-ink); }

  .rule {
    position: absolute;
    top: 196px; left: 0; right: 0;
    height: 1px;
    background: var(--rule-grey);
  }
  .contact {
    position: absolute;
    top: 210px; left: 0; right: 0;
    display: flex;
    justify-content: center;
    gap: 26px;
    font-style: italic;
    font-weight: 300;
    font-size: 13px;
    color: var(--text-grey);
    line-height: 20px;
  }
  .contact__address { text-align: right; }
  .contact__phone { display: flex; align-items: center; gap: 8px; }
  .contact__phone svg { width: 12px; height: 12px; fill: var(--navy-ink); }

  .web {
    position: absolute;
    top: 166px; left: 0; right: 0;
    text-align: center;
    font-style: italic;
    font-size: 12.5px;
    letter-spacing: 3px;
    color: #dcdcf0;
  }
</style>
</head>
<body>
  <section class="card card--front" aria-label="Business card front">
    <div class="wordmark">velmora partners</div>
    <div class="identity">
      <div class="identity__name">Luis R. Abadal</div>
      <div class="identity__company">Velmora Partners S.L.</div>
      <div class="identity__email">labadal@<strong>velmorapartners.com</strong></div>
    </div>
    <div class="rule"></div>
    <div class="contact">
      <div class="contact__address">
        Casa de Torrelumbre<br>
        Calle de Vientoalto 27<br>
        28014 Madrid
      </div>
      <div class="contact__phones">
        <div class="contact__phone">
          <svg viewBox="0 0 24 24" aria-hidden="true"><path d="M6.6 10.8a15.1 15.1 0 0 0 6.6 6.6l2.2-2.2a1 1 0 0 1 1-.25 11.4 11.4 0 0 0 3.6.57 1 1 0 0 1 1 1V20a1 1 0 0 1-1 1A17 17 0 0 1 3 4a1 1 0 0 1 1-1h3.5a1 1 0 0 1 1 1c0 1.25.2 2.45.57 3.6a1 1 0 0 1-.25 1z"/></svg>
          <span>+34 (91) 387-2265</span>
        </div>
        <div class="contact__phone">
          <svg viewBox="0 0 24 24" aria-hidden="true"><path d="M7 2h10a2 2 0 0 1 2 2v16a2 2 0 0 1-2 2H7a2 2 0 0 1-2-2V4a2 2 0 0 1 2-2zm0 3v12h10V5zm5 13.5a1 1 0 1 0 0 2 1 1 0 0 0 0-2z"/></svg>
          <span>+34 (646) 819-054</span>
        </div>
      </div>
    </div>
  </section>

  <section class="card card--back" aria-label="Business card back">
    <div class="wordmark">velmora partners</div>
    <div class="web">www.velmorapartners.com</div>
  </section>
</body>
</html>
```